Package Card - Horse Products

I require a card design for the top of a package (see photo). This product is a number holder that gets pinned on to a horse bridle or saddle blanket for competitions. It is a high quality, genuine leather, and premium product.Card is 15cm across and 6cm high. Requirements:Must have - Logo, -"Equestrian Number Holder"- Place on back for barcodeAnything else is up to you! Suggestions and ideas welcome. Card back colour can be any colour.My outcome is for it to look like a premium product

Target Market(s)

High end equestrian competitors

Colors
fbf289

Requirements
Must have
• Logo
• "Equestrian Number Holder"
• "Genuine Leather"
• Room on the back for a barcode sticker
Nice to have
• Should look up market and elegant

```html
<!DOCTYPE html>
<html lang="en">
<head>
<meta charset="utf-8">
<title>Harbor Crest Equestrian – Number Holder Package Card</title>
<link rel="stylesheet" href="https://fonts.googleapis.com/css2?family=Cinzel:wght@500;600&display=swap">
<style>
  :root {
    --backdrop: #d5d5d7;
    --card-black: #000000;
    --band-black: #0a0b0d;
    --panel-black: #0c0d0f;
    --gold-deep: #b8742e;
    --gold-mid: #d08f3d;
    --gold-light: #f3c46a;
    --white: #ffffff;
  }
  html, body {
    margin: 0;
    padding: 0;
    width: 1200px;
    height: 999px;
    overflow: hidden;
    background: var(--backdrop);
  }
  .package-card {
    position: relative;
    width: 1200px;
    height: 999px;
    font-family: "Cinzel", "Times New Roman", serif;
  }
  .card-art {
    position: absolute;
    inset: 0;
  }
  .hang-label {
    position: absolute;
    left: 0;
    width: 1200px;
    top: 340px;
    margin: 0;
    text-align: center;
    color: var(--white);
    font-size: 62px;
    font-weight: 600;
    letter-spacing: 1px;
    font-variant: small-caps;
    transform: rotate(180deg);
    line-height: 1;
  }
  .brand-name {
    position: absolute;
    left: 300px;
    width: 600px;
    top: 752px;
    margin: 0;
    display: flex;
    align-items: center;
    justify-content: center;
    gap: 16px;
    color: var(--white);
    font-size: 34px;
    font-weight: 500;
    letter-spacing: 3px;
    line-height: 1;
  }
  .brand-dot {
    width: 14px;
    height: 14px;
    border-radius: 50%;
    background: var(--white);
    flex: none;
  }
  .product-title {
    position: absolute;
    left: 0;
    width: 1200px;
    top: 858px;
    margin: 0;
    text-align: center;
    color: var(--white);
    font-size: 66px;
    font-weight: 600;
    font-variant: small-caps;
    letter-spacing: 0;
    line-height: 1;
  }
</style>
</head>
<body>
<main class="package-card">
  <svg class="card-art" width="1200" height="999" viewBox="0 0 1200 999" aria-hidden="true">
    <defs>
      <linearGradient id="gold-swoosh" x1="0" y1="0" x2="1" y2="0">
        <stop offset="0" stop-color="var(--gold-deep)"/>
        <stop offset="0.5" stop-color="var(--gold-mid)"/>
        <stop offset="0.85" stop-color="var(--gold-light)"/>
        <stop offset="1" stop-color="var(--gold-mid)"/>
      </linearGradient>
    </defs>
    <rect class="card-base" x="24" y="38" width="1152" height="922" fill="var(--card-black)"/>
    <path class="diagonal-band" d="M24 522 L1176 195 L1176 548 C1000 600 700 590 500 615 C300 640 120 720 24 800 Z" fill="var(--band-black)"/>
    <path class="gold-swoosh" d="M24 800 C120 720 300 640 500 615 C700 590 1000 600 1176 548 L1176 575 C1000 615 750 610 520 630 C320 650 140 720 24 800 Z" fill="url(#gold-swoosh)"/>
    <path class="brand-panel" d="M300 712 L750 668 L900 678 L900 876 L300 876 Z" fill="var(--panel-black)"/>
    <rect class="barcode-window" x="326" y="145" width="548" height="185" fill="var(--white)"/>
    <circle class="pin-hole" cx="600" cy="442" r="25" fill="var(--white)"/>
    <circle class="pin-hole" cx="600" cy="555" r="25" fill="var(--white)"/>
  </svg>

  <p class="hang-label">Genuine Leather</p>

  <h2 class="brand-name"><span class="brand-dot"></span>HARBOR CREST EQUESTRIAN</h2>

  <h1 class="product-title">Equestrian Number Holder</h1>
</main>
</body>
</html>
```